Plakat-Design für Tora-Unterricht einer Jüdischen Gemeinde
Zielgruppe
Wir sind die Jüdische Gemeinde.(vereinigte synagogengemeinde Halden.
Wir organisieren einen Tora-Unterricht.
Zielgruppe sind Gemeindemitglieder(Männer und Frauen)die meisten aus der ehemaligen Sowjetunion, 50 Jahre aufwärts. Russischsprachig.
Die Plakate sollen in der Gemeinde hängen und so viele wie es geht ansprechen.
Aufgabenstellung
Plakat in russischer Sprache. Im folgenden steht der Text mit deutscher Übersetzung. Die Übersetzung dient nur zu Ihrer Information/Orientierung. Nur bei der Zeile mit Anführungsstrichen bleibt der deutsche Text:
Цикл лекций с раввином Элиэзер Розенталь - Vortragsreihe von Rabbiner Elieser Rosenthal
'Иcточник жизни-Quelle des Lebens'
По четвергам в 13.00 - donnerstags um 13:00 Uhr
С переводом на русский язык Ирины Бережной - mit Übersetzung ins russische von Frau Irina Bereschnaja
Приходите все! - Alle sind herzlich willkommen!
Вас ожидают увлека тельные уроки Торы а также интересные путешествия и экскурсии.- Euch erwarten spannende Tora Unterrichte und auch interessante Ausflüge und Besichtigung

```html
<!DOCTYPE html>
<html lang="ru">
<head>
<meta charset="utf-8">
<title>Источник жизни – Quelle des Lebens</title>
<link rel="stylesheet" href="https://fonts.googleapis.com/css2?family=Alegreya+SC:wght@900&family=Ubuntu:wght@500&display=swap">
<style>
  :root {
    --stone-light: #ddd6cf;
    --stone-mid: #b9b2aa;
    --stone-dark: #8f8a84;
    --teal-deep: #0f5a4a;
    --teal-soft: #3f7f78;
    --amber: #c9923a;
    --ink-green: #12352a;
    --halo: #ffffff;
    --panel: rgba(255, 255, 255, 0.52);
  }
  html, body {
    margin: 0;
    padding: 0;
    width: 1200px;
    height: 849px;
    overflow: hidden;
    background: #ffffff;
  }
  .poster {
    position: relative;
    width: 1200px;
    height: 849px;
    overflow: hidden;
    background:
      radial-gradient(ellipse at 20% 30%, var(--stone-light) 0%, transparent 60%),
      radial-gradient(ellipse at 70% 80%, #e6ddd6 0%, transparent 55%),
      linear-gradient(135deg, var(--stone-mid) 0%, var(--stone-light) 45%, var(--stone-dark) 100%);
  }
  .backdrop {
    position: absolute;
    inset: 0;
  }
  .panel {
    position: absolute;
    left: 89px;
    top: 84px;
    width: 1029px;
    height: 691px;
    background: var(--panel);
  }
  .headline, .subline, .info {
    position: absolute;
    margin: 0;
    color: var(--ink-green);
    text-shadow:
      -2px 0 0 var(--halo), 2px 0 0 var(--halo),
      0 -2px 0 var(--halo), 0 2px 0 var(--halo),
      -2px -2px 0 var(--halo), 2px 2px 0 var(--halo),
      -2px 2px 0 var(--halo), 2px -2px 0 var(--halo);
    white-space: nowrap;
  }
  .headline {
    left: 164px;
    top: 134px;
    font-family: "Alegreya SC", Georgia, serif;
    font-weight: 900;
    font-size: 88px;
    line-height: 73px;
    letter-spacing: 1px;
  }
  .subline {
    right: 164px;
    top: 320px;
    font-family: "Ubuntu", Arial, sans-serif;
    font-weight: 500;
    font-variant: small-caps;
    font-size: 29px;
    letter-spacing: 2.2px;
  }
  .info {
    left: 166px;
    font-family: "Ubuntu", Arial, sans-serif;
    font-weight: 500;
    font-variant: small-caps;
    font-size: 41px;
    line-height: 48px;
    letter-spacing: 2.5px;
  }
  .info-time { top: 440px; }
  .info-translation { top: 520px; }
  .info-invite { top: 648px; }
</style>
</head>
<body>
  <main class="poster">
    <svg class="backdrop" width="1200" height="849" viewBox="0 0 1200 849" aria-hidden="true">
      <defs>
        <linearGradient id="bandTone" x1="0" y1="0" x2="1" y2="1">
          <stop offset="0" stop-color="#1b4d40"/>
          <stop offset="1" stop-color="#0b5c4a"/>
        </linearGradient>
        <radialGradient id="sceneTone" cx="0.6" cy="0.65" r="0.7">
          <stop offset="0" stop-color="#d9a45a" stop-opacity="0.85"/>
          <stop offset="0.45" stop-color="#6f958c" stop-opacity="0.75"/>
          <stop offset="1" stop-color="#3f7f78" stop-opacity="0"/>
        </radialGradient>
      </defs>
      <polygon class="accent-band" points="557,0 977,0 1200,330 1200,849 1076,849" fill="url(#bandTone)"/>
    </svg>

    <div class="panel"></div>

    <svg class="backdrop" width="1200" height="849" viewBox="0 0 1200 849">
      <rect class="scene-image" x="700" y="300" width="430" height="549" rx="40"
            fill="url(#sceneTone)" role="img"
            aria-label="Фотография: молящийся человек у окна с восточной звёздчатой решёткой"/>
    </svg>

    <h1 class="headline">Источник жизни<br>Quelle des Lebens</h1>
    <p class="subline">Цикл лекций с раввином Элиэзер Розенталь</p>

    <p class="info info-time">По четвергам в 13.00</p>
    <p class="info info-translation">С переводом на русский<br>язык Ирины Бережной</p>
    <p class="info info-invite">Приходите все!</p>
  </main>
</body>
</html>
```